Fresh Dwelling Tract Guide needs a new Landing Page

I like to get a landing page or website with 2-3 pages to help target home buyers who are looking to buy homes from builders such as TW Residences, Morvik, P.L. Fennick, etc. The landing page/website to be non-cluttered and be able to explain to home buyers that there are many benefits to include me as their buyer's agent when they buy a brand new home from any builders.
I may want to incorporate a short explanation video (animated) on the landing page and then for the viewer to click on a button that will take them to another page where they can search for new homes from different builders.
Target Market(s)
Home buyers looking to buy brand new home from builders such as TW Residences, Morvik, P.L. Fennick, etc.
Industry/Entity Type
Real Estate
Number of Pages Required
2 page
Font styles to use
Requirements
Must have
- The landing page may have the explanation video at the bottom of the landing page (scrolled down) or there may be a CALL TO ACTION button that takes the viewer to the 2nd page to watch the explanation video. Once they watched the explanation video and are still interested, they can click on another CALL TO ACTION button that will take them to another website that they will be able to search for all the available new homes and register their contact information.
Should not have
- No clutters and no dark colors.

```html
<!DOCTYPE html>
<html lang="en">
<head>
<meta charset="utf-8">
<title>Fresh Dwelling Tract Guide</title>
<link href="https://fonts.googleapis.com/css2?family=Mulish:wght@300;400;700&family=Open+Sans:wght@400&display=swap" rel="stylesheet">
<style>
  :root {
    --brand-blue: #1a4fb5;
    --hero-light: #4a7fe2;
    --hero-mid: #2b62d2;
    --hero-dark: #1a45a8;
    --white: #ffffff;
    --footer-text: #444444;
    --icon-grey: #555555;
  }
  * { box-sizing: border-box; margin: 0; padding: 0; }
  html, body {
    width: 1200px; height: 614px; overflow: hidden;
    background: var(--white);
  }
  .page {
    position: relative; width: 1200px; height: 614px;
    font-family: "Mulish", sans-serif;
  }
  .hero-backdrop {
    position: absolute; left: 0; top: 0;
    width: 1200px; height: 560px;
  }
  .site-title {
    position: absolute; top: 14px; left: 0; width: 100%;
    text-align: center; color: var(--white);
    font-weight: 700; font-size: 39px; letter-spacing: 0.2px;
  }
  .play-button {
    position: absolute; left: 581px; top: 206px;
    width: 38px; height: 38px;
  }
  .hero-heading {
    position: absolute; top: 256px; left: 0; width: 100%;
    text-align: center; color: var(--white);
    font-weight: 300; font-size: 32px;
  }
  .cta-button {
    position: absolute; left: 514px; top: 306px;
    width: 171px; height: 47px;
    background: var(--white); color: var(--brand-blue);
    display: flex; align-items: center; justify-content: center; gap: 10px;
    font-size: 19px; font-weight: 400; text-decoration: none;
    border-radius: 2px;
  }
  .cta-icon { width: 15px; height: 15px; }
  .site-footer {
    position: absolute; top: 575px; left: 134px; right: 134px;
    display: flex; justify-content: space-between; align-items: center;
  }
  .copyright {
    font-family: "Open Sans", sans-serif; font-size: 11.5px;
    color: var(--footer-text); word-spacing: 1px;
  }
  .social-links { display: flex; gap: 14px; }
  .social-links a {
    font-family: "Mulish", sans-serif; font-size: 12px; font-weight: 700;
    color: var(--icon-grey); text-decoration: none;
  }
</style>
</head>
<body>
<main class="page">
  <svg class="hero-backdrop" viewBox="0 0 1200 560" role="img" aria-label="Blue-toned photograph of a white Victorian house with a wraparound porch, tall trees and flowering shrubs">
    <defs>
      <linearGradient id="heroTone" x1="0" y1="0" x2="0" y2="1">
        <stop offset="0" stop-color="var(--hero-mid)"/>
        <stop offset="0.5" stop-color="var(--hero-light)"/>
        <stop offset="1" stop-color="var(--hero-dark)"/>
      </linearGradient>
    </defs>
    <path d="M0 0 H1200 V484 Q600 632 0 484 Z" fill="url(#heroTone)"/>
  </svg>

  <h1 class="site-title">Fresh Dwelling Tract Guide</h1>

  <svg class="play-button" viewBox="0 0 38 38" aria-label="Play video">
    <circle cx="19" cy="19" r="19" fill="var(--white)"/>
    <path d="M15 11.5 L27 19 L15 26.5 Z" fill="var(--brand-blue)" stroke="var(--brand-blue)" stroke-width="2" stroke-linejoin="round"/>
  </svg>

  <h2 class="hero-heading">Etiam mattis augue vehicula</h2>

  <a class="cta-button" href="#">
    Find A Home
    <svg class="cta-icon" viewBox="0 0 16 16" aria-hidden="true">
      <circle cx="8" cy="8" r="8" fill="var(--brand-blue)"/>
      <path d="M6.5 4.5 L10 8 L6.5 11.5" fill="none" stroke="var(--white)" stroke-width="2" stroke-linecap="round" stroke-linejoin="round"/>
    </svg>
  </a>

  <footer class="site-footer">
    <p class="copyright">Copyright &copy; 2018 Fresh Dwelling Tract Guide. &nbsp;All rights reserved.</p>
    <nav class="social-links">
      <a href="#">Friendlink</a>
      <a href="#">Chirpline</a>
    </nav>
  </footer>
</main>
</body>
</html>
```